Telecommunications Company needs a business card design

We are looking for a sleek, professional and modern business card design based off our new logo. Will look at both light and dark options. On some designs please provide a small space for a QR code

Target Market(s)

B2B clients in Australia

Contact Information for Business Card

Name, Position, Brisbane (head) office, Phone number, email address, QR code (link to our website qlinetelecom.com.au

Colors
0054AA
0677BA
7BADD7
CADEEF
E8F1F8
0094D4
00A9DD
6FCCEA
C7EBF8
E9F6FB
00AB8E
00BBA5
67D7C9
C6EFE9
E9F9F6

```html
<!DOCTYPE html>
<html lang="en">
<head>
<meta charset="UTF-8">
<title>Qline Telecom – Business Card</title>
<link href="https://fonts.googleapis.com/css2?family=Open+Sans:wght@400;600;700&display=swap" rel="stylesheet">
<style>
  :root {
    --stage: #2b2b2d;
    --blue-deep: #0054AA;
    --blue-mid: #0677BA;
    --blue-bright: #0094D4;
    --cyan: #00A9DD;
    --teal: #00AB8E;
    --teal-light: #00BBA5;
    --grey: #8a929c;
    --ink: #2a2a2a;
    --white: #ffffff;
  }
  * { margin: 0; padding: 0; box-sizing: border-box; }
  html, body {
    width: 1200px;
    height: 1015px;
    overflow: hidden;
    background: var(--stage);
    font-family: "Open Sans", Arial, sans-serif;
  }
  .canvas {
    position: relative;
    width: 1200px;
    height: 1015px;
  }
  .card {
    position: absolute;
    left: 250px;
    width: 700px;
    height: 400px;
    overflow: hidden;
  }
  .card--front {
    top: 80px;
    background: linear-gradient(160deg, var(--cyan) 0%, var(--blue-bright) 40%, var(--blue-mid) 75%, var(--blue-deep) 100%);
  }
  .card--back {
    top: 535px;
    background: var(--white);
  }
  .brand {
    position: absolute;
    display: flex;
    align-items: center;
    gap: 14px;
    font-weight: 700;
    letter-spacing: 2px;
    text-transform: uppercase;
    white-space: nowrap;
  }
  .brand__mark {
    width: 22px;
    height: 22px;
    flex: none;
  }
  .card--front .brand {
    left: 50%;
    top: 50%;
    transform: translate(-50%, -50%);
    font-size: 44px;
    color: var(--white);
  }
  .card--front .brand__mark { background: var(--white); }
  .card--back .brand {
    right: 50px;
    top: 120px;
    font-size: 34px;
    color: var(--blue-mid);
  }
  .card--back .brand__mark { background: var(--teal); }
  .contact {
    position: absolute;
    left: 62px;
    top: 150px;
    color: var(--ink);
  }
  .contact__accent {
    position: absolute;
    left: -62px;
    top: 8px;
    width: 34px;
    height: 36px;
    background: linear-gradient(180deg, var(--teal-light), var(--blue-bright));
  }
  .contact__name {
    font-size: 25px;
    font-weight: 700;
    color: var(--blue-mid);
    text-transform: uppercase;
    line-height: 1.1;
  }
  .contact__role {
    font-size: 17px;
    line-height: 1.3;
    margin-bottom: 10px;
  }
  .contact__list { list-style: none; }
  .contact__item {
    display: flex;
    align-items: center;
    gap: 10px;
    font-size: 17px;
    line-height: 1.45;
  }
  .contact__item svg { width: 16px; height: 16px; flex: none; }
  .contact__highlight { color: var(--blue-bright); }
  .contact__address {
    margin-top: 14px;
    margin-left: 26px;
    font-size: 17px;
    line-height: 1.35;
  }
</style>
</head>
<body>
<main class="canvas">

  <section class="card card--front" aria-label="Card front">
    <div class="brand"><span class="brand__mark"></span>Qline Telecom</div>
  </section>

  <section class="card card--back" aria-label="Card back">
    <div class="contact">
      <span class="contact__accent"></span>
      <h1 class="contact__name">Daniel Harper</h1>
      <p class="contact__role">Managing Director</p>
      <ul class="contact__list">
        <li class="contact__item">
          <svg viewBox="0 0 16 16" aria-hidden="true"><path fill="var(--blue-mid)" d="M3.5 1.5l2.5 0 1 3.5-1.6 1.2a8 8 0 0 0 4.4 4.4L11 9l3.5 1v2.5c0 1-1 2-2 2A11 11 0 0 1 1.5 3.5c0-1 1-2 2-2z"/></svg>
          07-3100 482 615
        </li>
        <li class="contact__item">
          <svg viewBox="0 0 16 16" aria-hidden="true"><rect x="1" y="3" width="14" height="10" fill="var(--blue-mid)"/><path d="M1 3l7 6 7-6" fill="none" stroke="#fff" stroke-width="1.3"/></svg>
          info@qlinetelecom.com.au
        </li>
        <li class="contact__item">
          <svg viewBox="0 0 16 16" aria-hidden="true"><circle cx="8" cy="8" r="7" fill="var(--blue-mid)"/><g fill="none" stroke="#fff" stroke-width="0.9"><ellipse cx="8" cy="8" rx="3" ry="7"/><path d="M1 8h14M2.2 4.5h11.6M2.2 11.5h11.6"/></g></svg>
          <span>www.<span class="contact__highlight">qlinetelecom</span>.com.au</span>
        </li>
      </ul>
      <p class="contact__address">218 Fairfield Road<br>Yeronga, Brisbane</p>
    </div>
    <div class="brand"><span class="brand__mark"></span>Qline Telecom</div>
  </section>

</main>
</body>
</html>
```